Thriller/Romance novel book cover design - Copper Tidewake

I need a book cover for a novel (print + ebook). Genre = thriller / romance. Title = Copper Tidewake. Author = Dorian Kell.
Story is set in Caribbean. 45-year-old Ex-OVK agent is hunted by corrupt politicians, OVK and cartel. He is a life-long fisherman and seaman who joined the Army after college and became a war hero, followed by 10 years as operative for the OVK. Betrayal from Washington saw him accused of killing his mentor/friend/OVK Director and he is now a fugitive. He has been hiding for 7 years on Grand Cayman, and lives a secluded, private life as a fisherman on his modern sportfisherman-style boat ('50 Velmora Convertible for reference). Boat name = Copper Tidewake (as in the playing card) represents fate to him and his high school sweetheart to whom he was engaged before a tragic event separated them. His main goal, beyond survival, is to reunite with his long, lost love, but he can't risk putting her in danger until he settles the case and those searching for him. The boat name (Copper Tidewake) only has relevance to him and his soulmate, who is not even aware that he is still alive.

Target Market(s)

thriller and romantic thriller readers

Requirements
Must have
• author name should be small on bottom of cover - not at top. Design is wide open for creative ideas. If a boat is used in artwork, it must be a modern sportfisherman style boat (google will define this
Nice to have
• I like intrigue and mystery. Don't try to explain or show too much. Prefer sunsets (orange, red, purple, yellow) to blue sky, blue water to give it a darker tone
Should not have
• do not want images of people on the cover like many romance novels do.

```html
<!DOCTYPE html>
<html lang="en">
<head>
<meta charset="utf-8">
<title>Copper Tidewake — Dorian Kell</title>
<link rel="stylesheet" href="https://fonts.googleapis.com/css2?family=Bodoni+Moda:wght@400;500&family=Josefin+Sans:wght@400&display=swap">
<style>
  :root {
    --page: #ffffff;
    --paper-light: #eadfc6;
    --paper-mid: #d7c39d;
    --paper-edge: #9c7a4c;
    --ink: #0d0b09;
    --sky-top: #3a1f4a;
    --sky-mid: #c4203a;
    --sky-glow: #f3b21c;
    --sea-dark: #1d1a2a;
  }
  html, body {
    margin: 0;
    width: 1200px;
    height: 1200px;
    overflow: hidden;
    background: var(--page);
  }
  .cover {
    position: absolute;
    left: 232px;
    top: 58px;
    width: 696px;
    height: 1110px;
    background:
      radial-gradient(ellipse at 50% 45%, var(--paper-light) 0%, var(--paper-mid) 65%, var(--paper-edge) 100%);
    overflow: hidden;
  }
  .cover-art {
    position: absolute;
    left: 0;
    top: 0;
    width: 696px;
    height: 1110px;
  }
  .title {
    position: absolute;
    margin: 0;
    font-family: "Bodoni Moda", "Didot", serif;
    font-weight: 400;
    color: var(--ink);
    line-height: 1;
    white-space: nowrap;
  }
  .title-line-one {
    top: 72px;
    left: 160px;
    font-size: 100px;
  }
  .title-line-two {
    top: 188px;
    left: 136px;
    font-size: 104px;
  }
  .corner-rank {
    position: absolute;
    width: 80px;
    height: 128px;
    text-align: center;
    font-family: "Josefin Sans", "Futura", sans-serif;
    color: var(--ink);
    font-size: 128px;
    line-height: 128px;
  }
  .corner-rank-top { left: 52px; top: 150px; }
  .corner-rank-bottom { left: 556px; top: 852px; transform: rotate(180deg); }
  .author {
    position: absolute;
    left: 0;
    width: 696px;
    top: 1010px;
    margin: 0;
    text-align: center;
    font-family: "Bodoni Moda", "Didot", serif;
    font-size: 40px;
    letter-spacing: 3px;
    color: var(--ink);
  }
</style>
</head>
<body>
  <main class="cover">
    <svg class="cover-art" viewBox="0 0 696 1110" xmlns="http://www.w3.org/2000/svg">
      <defs>
        <linearGradient id="sunset" x1="0" y1="0" x2="0" y2="1">
          <stop offset="0" stop-color="var(--sky-top)"/>
          <stop offset="0.25" stop-color="var(--sky-mid)"/>
          <stop offset="0.5" stop-color="var(--sky-glow)"/>
          <stop offset="0.62" stop-color="#e2461f"/>
          <stop offset="1" stop-color="var(--sea-dark)"/>
        </linearGradient>
      </defs>
      <path class="torn-edge" fill="#6b4a2a" opacity="0.55"
        d="M198 318 L250 300 L300 306 L352 292 L406 318 L470 300 L520 330 L540 372 L560 420 L560 480 L584 530 L600 590 L576 640 L548 690 L510 730 L472 770 L440 810 L420 830 L350 812 L300 790 L262 740 L216 700 L180 640 L120 556 L140 510 L148 470 L172 430 L176 380 Z"/>
      <path class="window-scene" role="img" aria-label="Sportfishing boat at anchor on calm sea under a red, orange and purple sunset"
        fill="url(#sunset)"
        d="M204 326 L252 308 L300 314 L352 300 L404 326 L466 308 L514 338 L532 378 L552 424 L552 482 L574 532 L590 590 L568 636 L540 684 L504 724 L466 764 L436 802 L418 820 L352 804 L304 782 L268 734 L222 694 L188 636 L130 556 L148 512 L156 472 L180 432 L184 382 Z"/>
      <g class="club club-centre" fill="var(--ink)">
        <path d="M338 880 L326 826 L350 826 Z"/>
        <circle cx="338" cy="852" r="40"/>
        <circle cx="296" cy="920" r="40"/>
        <circle cx="380" cy="920" r="40"/>
        <circle cx="338" cy="900" r="22"/>
      </g>
      <g class="club club-corner-top" fill="var(--ink)">
        <circle cx="92" cy="298" r="18"/>
        <circle cx="72" cy="326" r="18"/>
        <circle cx="112" cy="326" r="18"/>
        <path d="M92 310 L82 362 L102 362 Z"/>
      </g>
      <g class="club club-corner-bottom" fill="var(--ink)">
        <path d="M596 800 L586 752 L606 752 Z"/>
        <circle cx="576" cy="796" r="18"/>
        <circle cx="616" cy="796" r="18"/>
        <circle cx="596" cy="824" r="18"/>
      </g>
    </svg>
    <span class="corner-rank corner-rank-top">3</span>
    <span class="corner-rank corner-rank-bottom">3</span>
    <h1 class="title title-line-one">Copper</h1>
    <h1 class="title title-line-two">Tidewake</h1>
    <p class="author">Dorian Kell</p>
  </main>
</body>
</html>
```